business card

Business card for new business.
Red and black corporate colors.
Card can have an Indsutrial feel to it. Feel free to add Rust, Bolted steel, or graphics as you see fit. We provide highly specialized services to the below mentioned industries.
Keep information out of corners so that if I want I can choose rounded corners.
Information
- front. name - title - phone - email
- Rear
Fabrication - Pipelines - Utilities - Marine - Power
Northgate - Riverton - Cedar Falls - Ashford - Harbourview

```html
<!DOCTYPE html>
<html lang="en">
<head>
<meta charset="utf-8">
<title>Ironspan Business Card</title>
<link href="https://fonts.googleapis.com/css2?family=Work+Sans:wght@400;500;600;800&display=swap" rel="stylesheet">
<style>
  :root {
    --bg: #1f2124;
    --card-back: #6c6c70;
    --card-front: #ffffff;
    --map-tone: #7c7c80;
    --red: #e0141e;
    --ink: #5a5a5e;
    --white: #ffffff;
  }
  * { box-sizing: border-box; margin: 0; padding: 0; }
  html, body { width: 1200px; height: 738px; overflow: hidden; }
  body {
    background: var(--bg);
    font-family: "Work Sans", Arial, sans-serif;
    display: flex;
    align-items: center;
    justify-content: center;
    gap: 44px;
  }
  .card {
    width: 520px;
    height: 298px;
    position: relative;
    box-shadow: 0 10px 30px rgba(0,0,0,.45);
  }
  /* Back */
  .card--back { background: var(--card-back); color: var(--white); }
  .world-map {
    position: absolute;
    left: 40px; top: 24px;
    width: 440px; height: 190px;
    background: radial-gradient(ellipse at center, var(--map-tone) 0%, rgba(124,124,128,.4) 55%, rgba(108,108,112,0) 75%);
  }
  .back-brand {
    position: absolute;
    left: 0; right: 0; top: 92px;
    text-align: center;
    font-weight: 800;
    font-size: 50px;
    letter-spacing: 1px;
    color: var(--white);
  }
  .back-lines {
    position: absolute;
    left: 0; right: 0; bottom: 40px;
    text-align: center;
    font-size: 12.5px;
    line-height: 1.45;
    letter-spacing: .3px;
  }
  /* Front */
  .card--front { background: var(--card-front); color: var(--ink); }
  .front-brand {
    position: absolute;
    right: 40px; top: 30px;
    font-weight: 800;
    font-size: 34px;
    letter-spacing: .5px;
    color: var(--red);
  }
  .divider {
    position: absolute;
    left: 50px; right: 40px; top: 110px;
    height: 1.5px;
    background: var(--red);
  }
  .person { position: absolute; left: 50px; top: 124px; }
  .person__name {
    color: var(--red);
    font-weight: 500;
    font-size: 19px;
    letter-spacing: .5px;
  }
  .person__title { font-size: 13px; margin-top: 1px; }
  .address { position: absolute; left: 50px; top: 176px; font-size: 13.5px; line-height: 1.35; letter-spacing: .4px; }
  .contacts { position: absolute; left: 50px; top: 218px; list-style: none; font-size: 13.5px; line-height: 1.35; letter-spacing: .4px; }
  .contacts li { display: flex; align-items: center; gap: 9px; }
  .contacts svg { width: 9px; height: 9px; fill: none; stroke: var(--red); stroke-width: 1.6; flex: none; }
  .accent { color: var(--red); }
</style>
</head>
<body>
  <section class="card card--back" aria-label="Card back">
    <div class="world-map" role="img" aria-label="Dotted world map background"></div>
    <div class="back-brand">IRONSPAN</div>
    <p class="back-lines">
      Fabrication - Pipelines - Utilities - Marine - Power<br>
      Northgate - Riverton - Cedar Falls - Ashford - Harbourview
    </p>
  </section>

  <section class="card card--front" aria-label="Card front">
    <div class="front-brand">IRONSPAN</div>
    <div class="divider"></div>
    <div class="person">
      <div class="person__name">DANIEL BROOKS</div>
      <div class="person__title">Director</div>
    </div>
    <p class="address">1250 Ridge Park Rd.<br>Denver, CO 80203</p>
    <ul class="contacts">
      <li><svg viewBox="0 0 10 10"><path d="M2 1 L4 3 L3 4.5 Q4.5 6.5 5.5 7 L7 6 L9 8 L7.5 9.3 Q3 8 0.8 2.5 Z"/></svg><span>+1 555 014-2290</span></li>
      <li><svg viewBox="0 0 10 10"><rect x="1" y="2" width="8" height="6"/><path d="M1 2 L5 5.5 L9 2"/></svg><span>info@ironspan.com</span></li>
      <li><svg viewBox="0 0 10 10"><circle cx="5" cy="5" r="4"/><path d="M1 5 H9 M5 1 Q2.5 5 5 9 M5 1 Q7.5 5 5 9"/></svg><span>www.<span class="accent">ironspan</span>.com</span></li>
    </ul>
  </section>
</body>
</html>
```